Residential Remodeling Contractor needs updated business card

I need a new design for my business card.
Name of the company is Ridgefell Construction. I need a card that commands presence, strength, integrity. I have been in business for 28 years. I am a Residential Remodeling Contractor that covers all aspects of a residential remodel and build.

```html
<!DOCTYPE html>
<html lang="en">
<head>
<meta charset="utf-8">
<title>Ridgefell Construction – Business Card</title>
<link rel="stylesheet" href="https://fonts.googleapis.com/css2?family=Libre+Baskerville:wght@700&family=Arimo:ital,wght@0,400;0,700;1,400&display=swap">
<style>
  :root {
    --navy: #1b3f7e;
    --paper: #ffffff;
    --ink: #2f2f33;
    --backdrop: #2b2b2d;
  }
  * { margin: 0; padding: 0; box-sizing: border-box; }
  html, body {
    width: 1200px; height: 878px; overflow: hidden;
    background: var(--backdrop);
  }
  .stage {
    width: 1200px; height: 878px;
    display: flex; flex-direction: column; align-items: center; justify-content: center;
    gap: 40px;
  }
  .card {
    width: 640px; height: 366px; position: relative;
    box-shadow: 0 10px 30px rgba(0,0,0,.45);
  }
  .card-front {
    background: var(--navy);
    display: flex; align-items: center; justify-content: center;
  }
  .card-back { background: var(--paper); }

  .brand {
    display: flex; align-items: center;
    font-family: "Arimo", Arial, sans-serif;
    font-weight: 700;
    white-space: nowrap;
  }
  .brand-square { flex: none; }
  .card-front .brand { gap: 18px; color: var(--paper); font-size: 36px; }
  .card-front .brand-square { width: 36px; height: 36px; background: var(--paper); }
  .card-back .brand {
    position: absolute; right: 36px; bottom: 50px;
    gap: 12px; color: var(--navy); font-size: 22px;
  }
  .card-back .brand-square { width: 22px; height: 22px; background: var(--navy); }

  .name-block { position: absolute; left: 0; top: 40px; }
  .name-accent {
    position: absolute; left: 0; top: 0;
    width: 24px; height: 34px; background: var(--navy);
  }
  .person-name {
    position: absolute; left: 38px; top: 2px; white-space: nowrap;
    font-family: "Libre Baskerville", Georgia, serif; font-weight: 700;
    font-size: 22px; color: var(--navy); letter-spacing: .5px;
  }
  .person-title {
    position: absolute; left: 38px; top: 30px; white-space: nowrap;
    font-family: "Arimo", Arial, sans-serif; font-style: italic;
    font-size: 13px; color: var(--ink);
  }
  .address {
    position: absolute; left: 40px; top: 140px;
    font-family: "Arimo", Arial, sans-serif; font-style: italic;
    font-size: 14px; line-height: 1.5; color: var(--ink);
  }
  .contacts {
    position: absolute; left: 40px; top: 252px; list-style: none;
    font-family: "Arimo", Arial, sans-serif; font-style: italic;
    font-size: 14px; line-height: 1.75; color: var(--ink);
  }
  .contacts li { display: flex; align-items: center; gap: 9px; }
  .contacts svg { width: 12px; height: 12px; fill: var(--navy); flex: none; }
</style>
</head>
<body>
<main class="stage">
  <section class="card card-front" aria-label="Card front">
    <div class="brand"><span class="brand-square"></span><span>Ridgefell Construction</span></div>
  </section>

  <section class="card card-back" aria-label="Card back">
    <div class="name-block">
      <div class="name-accent"></div>
      <div class="person-name">DANIEL OKAFOR</div>
      <div class="person-title">Owner &amp; Manager</div>
    </div>

    <address class="address">
      P.O. Box&nbsp; Street Name<br>
      Country Name AB, A5B 521
    </address>

    <ul class="contacts">
      <li>
        <svg viewBox="0 0 12 12" aria-hidden="true"><path d="M1 4c0-2 2-3 5-3s5 1 5 3H8.5V3h-5v1zM2.5 5h7l1 6h-9z"/></svg>
        555 014 2286
      </li>
      <li>
        <svg viewBox="0 0 12 12" aria-hidden="true"><path d="M0 2h12v8H0zM1 3l5 4 5-4z" fill-rule="evenodd"/></svg>
        info@ridgefellconstruction.com
      </li>
      <li>
        <svg viewBox="0 0 12 12" aria-hidden="true"><circle cx="6" cy="6" r="5.5"/></svg>
        www.ridgefellconstruction.com
      </li>
    </ul>

    <div class="brand"><span class="brand-square"></span><span>Ridgefell Construction</span></div>
  </section>
</main>
</body>
</html>
```